New business card/stationary for a consulting company

I am looking for a clean and very professional looking business card for my consulting company as well as corresponding stationary. I am uploading our logo. I like simple and powerful for the feel. No graphics but I am open on everything else. Below is my contact information but would like the final to be in a version I can add my employees information into and print. Thank you.

Daniel Whitcombe
dan@ferncliffadvisory.com
2870 North 9th Avenue, Summit Floor, Elm Ridge, Illinois 60531
www.ferncliffadvisory.com

Industry/Entity Type

Consulting

Contact Information for Business Card

Daniel Whitcombe
dan@ferncliffadvisory.com
www.ferncliffadvisory.com

Font styles to use
Serif
Sans Serif

Requirements
Must have
• Our logo and the business card details.
Nice to have
• our website www.ferncliffadvisory.com

```html
<!DOCTYPE html>
<html lang="en">
<head>
<meta charset="utf-8">
<title>Ferncliff Advisory — Business Card</title>
<link rel="stylesheet" href="https://fonts.googleapis.com/css2?family=Marcellus&family=Roboto:wght@400&display=swap">
<style>
  :root {
    --backdrop: #e9e6e1;
    --card: #f7f7f6;
    --card-edge: #dcdcda;
    --navy: #1f3466;
    --ink: #2b2b2e;
  }
  html, body {
    margin: 0;
    padding: 0;
    width: 1200px;
    height: 970px;
    overflow: hidden;
    background: var(--backdrop);
  }
  .business-card {
    position: absolute;
    left: 172px;
    top: 270px;
    width: 856px;
    height: 476px;
    background: var(--card);
    border: 1px solid var(--card-edge);
    border-radius: 4px;
    box-shadow: 0 10px 30px rgba(0, 0, 0, 0.12);
  }
  .brand {
    position: absolute;
    left: 69px;
    top: 220px;
    display: flex;
    align-items: center;
    gap: 14px;
  }
  .brand-square {
    width: 22px;
    height: 22px;
    background: var(--navy);
  }
  .brand-name {
    font-family: "Marcellus", serif;
    font-size: 30px;
    color: var(--navy);
    letter-spacing: 0.5px;
    white-space: nowrap;
  }
  .contact {
    position: absolute;
    left: 442px;
    top: 152px;
    font-family: "Roboto", sans-serif;
    color: var(--ink);
  }
  .person-name {
    margin: 0 0 12px 0;
    font-family: "Marcellus", serif;
    font-weight: 400;
    font-size: 26px;
    letter-spacing: 1.2px;
    text-transform: uppercase;
    color: var(--navy);
  }
  .contact-line {
    display: flex;
    align-items: center;
    gap: 16px;
    font-size: 20px;
    line-height: 31px;
    white-space: nowrap;
  }
  .contact-icon {
    width: 20px;
    height: 20px;
    flex: none;
  }
  .address {
    margin: 10px 0 0 0;
    font-size: 20px;
    line-height: 32px;
    font-style: normal;
  }
</style>
</head>
<body>
  <div class="business-card">
    <div class="brand">
      <div class="brand-square"></div>
      <div class="brand-name">Ferncliff Advisory</div>
    </div>

    <div class="contact">
      <h1 class="person-name">Daniel Whitcombe</h1>
      <div class="contact-line">
        <svg class="contact-icon" viewBox="0 0 20 20" aria-hidden="true">
          <rect x="2" y="5" width="16" height="11" fill="#2b2b2e"/>
          <polyline points="2.5,5.5 10,11 17.5,5.5" fill="none" stroke="#f7f7f6" stroke-width="1.4"/>
        </svg>
        <span>dan@ferncliffadvisory.com</span>
      </div>
      <div class="contact-line">
        <svg class="contact-icon" viewBox="0 0 20 20" aria-hidden="true">
          <circle cx="10" cy="10" r="7" fill="none" stroke="#2b2b2e" stroke-width="1.6"/>
          <ellipse cx="10" cy="10" rx="3" ry="7" fill="none" stroke="#2b2b2e" stroke-width="1.3"/>
          <line x1="3" y1="10" x2="17" y2="10" stroke="#2b2b2e" stroke-width="1.3"/>
        </svg>
        <span>www.ferncliffadvisory.com</span>
      </div>
      <address class="address">2870 North 9th Avenue, Summit<br>Floor, Elm Ridge, Illinois 60531</address>
    </div>
  </div>
</body>
</html>
```